"Velmora Crest" sexual performance enhancement pill bottle label needed.

This should be interesting...

I am starting a line of sexual performance enhancement products. This will be the first of several products basically. Keep in mind, I am the type of business person to stay with one company for years if they provide me with quality work.

This particular product is a male sexual performance pill. The name of the product is "Velmora Crest." The packaging of the pills are a black bottle with a white top. Label on the product example would be perfect but at a minimum I have attached a "template" for your guidance.

Some of the technical aspects of this are as follows:

-File Format: Illustrator CS6 is preferred. (Winner must provide artwork in layer and can not flatten artwork.)
-Resolution: 300 dpi minimum
-Bleed: 1/16th (0.0625") inch from edge of label
-Color Mode: CMYK only or must be converted to CMYK for final production

Lastly, this is your project as a designer, artist, creator, this is essentially a piece of you that will be sold and known by thousands of people. I have no color scheme that I prefer, just use the template and follow the layout. If you have any further questions, please feel free to contact me at any time.
Updates

Quick note on the product and what it does: -Powerful, long lasting, harder erections -Works in a minutes and last for hours -Enhances sexual desire and drive Thank you for your ideas...

Project Deadline Extended
Reason: We decided to extent the project for a few more days to let the last few concepts come in. So far things are looking really good and we definitely have seen some amazing designs. Thank you for your hard work and amazing creativity. Looking forward to seeing what we have come in the next couple of day. Very respectfully, Brev

ONLY THREE DAYS LEFT!!!! Please submit your ideas as soon as possible. And as always, thank you for your help!!! V/r, Brev

Industry/Entity Type

Graphic Design

```html
<!DOCTYPE html>
<html lang="en">
<head>
<meta charset="utf-8">
<title>Velmora Crest Pill – Label</title>
<link href="https://fonts.googleapis.com/css2?family=Oswald:wght@500;600&display=swap" rel="stylesheet">
<style>
  :root {
    --backdrop-light: #d4d4d4;
    --backdrop-dark: #7a7a7a;
    --label-black: #16181b;
    --label-charcoal: #3a3d42;
    --accent-blue: #2f86d6;
    --band-blue: #3fb4ea;
    --band-blue-light: #5cc6f2;
    --navy-text: #0f3a66;
    --white: #ffffff;
    --pill-silver: #e4e6e9;
    --pill-text: #1c5fa8;
  }
  * { margin: 0; padding: 0; box-sizing: border-box; }
  html, body { width: 1200px; height: 900px; overflow: hidden; }
  body {
    background: radial-gradient(ellipse at 50% 40%, var(--backdrop-light) 0%, #a8a8a8 55%, var(--backdrop-dark) 100%);
    font-family: "Oswald", "Arial Narrow", sans-serif;
    display: flex;
    align-items: center;
    justify-content: center;
  }
  .label {
    position: relative;
    width: 820px;
    height: 470px;
    background: var(--label-black);
    overflow: hidden;
  }
  .label__texture {
    position: absolute;
    inset: 0;
    background: radial-gradient(ellipse at 50% 35%, var(--label-charcoal) 0%, #25282c 55%, var(--label-black) 100%);
  }
  .label__rule {
    position: absolute;
    left: 0; right: 0;
    height: 4px;
    background: var(--accent-blue);
  }
  .label__rule--top { top: 14px; }
  .label__rule--bottom { bottom: 14px; }
  .brand {
    position: absolute;
    top: 64px;
    left: 50%;
    transform: translateX(-50%);
    display: flex;
    align-items: center;
    gap: 14px;
  }
  .brand__name {
    background: var(--pill-silver);
    color: var(--pill-text);
    font-weight: 600;
    font-size: 40px;
    line-height: 1;
    letter-spacing: 0.5px;
    text-transform: uppercase;
    padding: 12px 30px 14px;
    border-radius: 36px;
    white-space: nowrap;
  }
  .brand__mark {
    width: 78px;
    height: 78px;
    border-radius: 50%;
    background: var(--pill-silver);
  }
  .product-name {
    position: absolute;
    top: 178px;
    left: 0; right: 0;
    text-align: center;
    color: var(--white);
    font-weight: 600;
    font-size: 48px;
    line-height: 1.15;
    text-transform: uppercase;
  }
  .claim-band {
    position: absolute;
    top: 322px;
    left: 0; right: 0;
    height: 66px;
    background: linear-gradient(180deg, var(--band-blue-light), var(--band-blue));
    display: flex;
    flex-direction: column;
    align-items: center;
    justify-content: center;
    color: var(--navy-text);
    font-weight: 600;
    font-size: 21px;
    line-height: 1.1;
    text-transform: uppercase;
  }
  .supplement-facts {
    position: absolute;
    top: 406px;
    left: 0; right: 0;
    text-align: center;
    color: var(--white);
    font-weight: 500;
    font-size: 15px;
    letter-spacing: 0.3px;
    text-transform: uppercase;
  }
</style>
</head>
<body>
  <section class="label">
    <div class="label__texture" role="img" aria-label="Dark perforated hexagon texture background"></div>
    <div class="label__rule label__rule--top"></div>
    <div class="label__rule label__rule--bottom"></div>

    <div class="brand">
      <span class="brand__name">Velmora Crest Pill</span>
      <span class="brand__mark"></span>
    </div>

    <h1 class="product-name">Horny Goat Weed<br>1600</h1>

    <div class="claim-band">
      <span>Max Strength!</span>
      <span>Pure and Potent*</span>
    </div>

    <p class="supplement-facts">Dietary Supplement · 60 Capsules</p>
  </section>
</body>
</html>
```